Tech business card design

We need an amazing business card design for our new business 'Pexla' a marketing tech startup based in Sydney, Australia. We provide an online marketplace for businesses to search and buy advertising media, connect with service providers and learn more about marketing. We wish to communicate 'cool tech', reliability and professionalism and design based around our logo.

Target Market(s)

Business Owners

Contact Information for Business Card

Name
Position
Email Address
Website
Phone Number

Font styles to use
Other font styles liked:
• Avenir & Avenir Next

Colors

Designer to choose colors to be used in the design.

```html
<!DOCTYPE html>
<html lang="en">
<head>
<meta charset="utf-8">
<title>Pexla business card</title>
<link href="https://fonts.googleapis.com/css2?family=Lato:wght@400;700;900&display=swap" rel="stylesheet">
<style>
  :root {
    --navy: #13143f;
    --navy-deep: #0e0e3a;
    --paper: #ffffff;
    --grey: #6b6b76;
    --backdrop: #e9e7e3;
  }
  * { margin: 0; padding: 0; box-sizing: border-box; }
  html, body { width: 1200px; height: 900px; overflow: hidden; }
  body {
    background: var(--backdrop);
    font-family: "Lato", Arial, sans-serif;
    position: relative;
  }
  .card {
    position: absolute;
    width: 560px;
    height: 320px;
    left: 320px;
    border-radius: 2px;
    overflow: hidden;
    box-shadow: 0 8px 24px rgba(0,0,0,0.18);
  }
  .card--back { top: 100px; background: var(--navy-deep); }
  .card--front { top: 470px; background: var(--paper); }

  .wordmark {
    font-family: "Lato", Arial, sans-serif;
    font-weight: 900;
    letter-spacing: -1px;
    line-height: 1;
    position: absolute;
  }
  .card--back .wordmark {
    color: var(--paper);
    font-size: 86px;
    left: 0; right: 0; top: 92px;
    text-align: center;
  }
  .card--back .site {
    position: absolute;
    left: 0; right: 0; bottom: 42px;
    text-align: center;
    color: var(--paper);
    font-size: 15px;
    letter-spacing: 0.5px;
  }

  .card--front .wordmark {
    color: var(--navy);
    font-size: 74px;
    left: 318px; top: 70px;
  }
  .holder { position: absolute; left: 40px; top: 74px; }
  .holder__name {
    color: var(--navy);
    font-weight: 700;
    font-size: 22px;
    letter-spacing: 0.8px;
    text-transform: uppercase;
  }
  .holder__role { color: var(--grey); font-size: 15px; margin-top: 2px; }

  .wave { position: absolute; inset: 0; width: 560px; height: 320px; }

  .contacts { position: absolute; left: 44px; top: 180px; list-style: none; }
  .contacts li {
    display: flex; align-items: center;
    color: var(--grey);
    font-size: 16px;
    line-height: 24px;
  }
  .contacts svg { width: 13px; height: 13px; margin-right: 8px; fill: var(--navy); }
</style>
</head>
<body>

  <section class="card card--back">
    <div class="wordmark">Pexla</div>
    <div class="site">www.pexlahub.com</div>
  </section>

  <section class="card card--front">
    <svg class="wave" viewBox="0 0 560 320" aria-hidden="true">
      <path d="M0 320 L0 292 C130 318 260 300 370 240 C440 200 500 178 560 170 L560 320 Z" fill="var(--navy)"/>
      <path d="M20 312 C170 306 280 270 380 220 C430 196 470 184 500 178" fill="none" stroke="var(--paper)" stroke-width="2.5"/>
    </svg>

    <div class="holder">
      <div class="holder__name">Marcus Hale</div>
      <div class="holder__role">Managing Director</div>
    </div>

    <div class="wordmark">Pexla</div>

    <ul class="contacts">
      <li>
        <svg viewBox="0 0 16 16"><path d="M3 2h3l1.5 3.5-2 1.3a8 8 0 0 0 3.7 3.7l1.3-2L14 10v3a1 1 0 0 1-1 1A11 11 0 0 1 2 3a1 1 0 0 1 1-1z"/></svg>
        044-987 654 321
      </li>
      <li>
        <svg viewBox="0 0 16 16"><path d="M1 3h14v10H1z M2 4.2v.6l6 4 6-4v-.6z" fill-rule="evenodd"/></svg>
        hello@pexlahub.com
      </li>
      <li>
        <svg viewBox="0 0 16 16"><circle cx="8" cy="8" r="7"/></svg>
        www.pexlahub.com
      </li>
    </ul>
  </section>

</body>
</html>
```